Business Card for a Creative Technology based HR services company

Our company name is Lumo8, and we build large communities of HR (human resource) and finance personnels through our mobile platform, and we conduct lots of on-line and off-line activities to get everyone constantly connected. Behind all these, we will also provide on-site HR and finance contractors to our clients, plus a host of other HR-related services. No process in our company takes more than 5-steps.
Our company slogan: Connecting Every Career
Target Market(s)
All human resource (HR) and finance personnels, from new entrants to highly experienced senior professionals.
Industry/Entity Type
Finance
Colors
Designer to choose colors to be used in the design.
Look and feel
Each slider illustrates characteristics of the customer's brand and the style your logo design should communicate.

```html
<!DOCTYPE html>
<html lang="en">
<head>
<meta charset="UTF-8">
<title>Lumo8 Business Card</title>
<link rel="stylesheet" href="https://fonts.googleapis.com/css2?family=Cinzel:wght@400;600&family=Josefin+Sans:wght@400;700&display=swap">
<style>
  :root {
    --navy: #0f2d55;
    --navy-faint: #15375f;
    --red: #e31b1b;
    --paper: #f6f6f6;
    --ink: #2b2b2b;
    --muted: #5a5a5a;
    --rule: #b9b9b9;
    --slogan: #dfe6f0;
    --backdrop: #e4e2de;
  }
  html, body {
    margin: 0;
    width: 1200px;
    height: 900px;
    overflow: hidden;
    background: var(--backdrop);
  }
  .canvas {
    position: relative;
    width: 1200px;
    height: 900px;
  }
  .card {
    position: absolute;
    left: 250px;
    width: 700px;
    height: 400px;
    overflow: hidden;
    box-shadow: 0 6px 18px rgba(0,0,0,0.18);
  }

  /* Back side */
  .card-back {
    top: 30px;
    background: var(--navy);
  }
  .back-watermark {
    position: absolute;
    left: 60px;
    top: -10px;
    font-family: "Josefin Sans", sans-serif;
    font-weight: 700;
    font-size: 190px;
    line-height: 1;
    letter-spacing: -4px;
    color: var(--navy-faint);
    white-space: nowrap;
  }
  .back-slogan {
    position: absolute;
    left: 50px;
    top: 200px;
    font-family: "Josefin Sans", sans-serif;
    font-size: 13px;
    letter-spacing: 4px;
    text-transform: uppercase;
    color: var(--slogan);
  }
  .back-brand {
    position: absolute;
    right: 60px;
    bottom: 70px;
    font-family: "Josefin Sans", sans-serif;
    font-weight: 700;
    font-size: 60px;
    line-height: 1;
    letter-spacing: -1px;
    color: #ffffff;
  }

  /* Front side */
  .card-front {
    top: 470px;
    background: var(--paper);
  }
  .swoosh {
    position: absolute;
    left: 0;
    top: 0;
  }
  .front-brand {
    position: absolute;
    left: 55px;
    top: 36px;
    font-family: "Josefin Sans", sans-serif;
    font-weight: 700;
    font-size: 48px;
    line-height: 1;
    letter-spacing: -1px;
    color: var(--navy);
  }
  .front-rule {
    position: absolute;
    left: 150px;
    top: 112px;
    width: 320px;
    height: 1px;
    background: var(--rule);
  }
  .address {
    position: absolute;
    left: 55px;
    top: 150px;
    font-family: "Josefin Sans", sans-serif;
    font-style: normal;
    font-size: 12px;
    line-height: 1.9;
    letter-spacing: 2px;
    text-transform: uppercase;
    color: var(--muted);
  }
  .person {
    position: absolute;
    right: 190px;
    top: 190px;
    text-align: right;
  }
  .person-name {
    font-family: "Cinzel", serif;
    font-weight: 600;
    font-size: 21px;
    letter-spacing: 3px;
    color: var(--ink);
  }
  .person-title {
    margin-top: 2px;
    font-family: "Cinzel", serif;
    font-weight: 600;
    font-size: 14px;
    letter-spacing: 2px;
    color: var(--navy);
  }
  .contacts {
    position: absolute;
    right: 190px;
    top: 256px;
    margin: 0;
    padding: 0;
    list-style: none;
    font-family: "Josefin Sans", sans-serif;
    font-size: 13px;
    letter-spacing: 2px;
    color: var(--muted);
  }
  .contacts li {
    display: flex;
    justify-content: flex-end;
    align-items: center;
    gap: 12px;
    height: 22px;
  }
  .contacts svg {
    width: 14px;
    height: 14px;
    fill: none;
    stroke: var(--red);
    stroke-width: 1.6;
  }
</style>
</head>
<body>
<main class="canvas">

  <section class="card card-back" aria-label="Card back">
    <div class="back-watermark" aria-hidden="true">Lumo8</div>
    <div class="back-slogan">Connecting Every Career</div>
    <div class="back-brand">Lumo8</div>
  </section>

  <section class="card card-front" aria-label="Card front">
    <svg class="swoosh" width="700" height="400" viewBox="0 0 700 400" aria-hidden="true">
      <path d="M425,400 C530,330 610,230 635,95 L700,85 L700,400 Z" fill="var(--navy)"/>
      <path d="M448,400 C548,330 622,235 646,95 L700,88 L700,400 Z" fill="var(--paper)"/>
      <path d="M470,400 C565,332 634,240 660,92 L700,86 L700,400 Z" fill="var(--red)"/>
    </svg>

    <div class="front-brand">Lumo8</div>
    <div class="front-rule"></div>

    <address class="address">
      4120 Alder Park Rd, Suite #7<br>
      Fairbrook, CA 95011
    </address>

    <div class="person">
      <div class="person-name">Nora Vance</div>
      <div class="person-title">CEO</div>
    </div>

    <ul class="contacts">
      <li>555-402-1187
        <svg viewBox="0 0 14 14"><path d="M3 2 L5 2 L6 5 L4.5 6 C5.5 8 6 8.5 8 9.5 L9 8 L12 9 L12 11 C7 12 2 7 3 2 Z"/></svg>
      </li>
      <li>555-618-3340
        <svg viewBox="0 0 14 14"><rect x="4" y="1.5" width="6" height="11" rx="1"/><line x1="6" y1="10.5" x2="8" y2="10.5"/></svg>
      </li>
      <li>555-277-9012
        <svg viewBox="0 0 14 14"><rect x="4" y="1.5" width="6" height="4"/><rect x="1.5" y="5.5" width="11" height="5"/><rect x="4" y="9" width="6" height="3.5"/></svg>
      </li>
      <li>nvance@lumo8.com
        <svg viewBox="0 0 14 14"><rect x="1.5" y="3" width="11" height="8"/><path d="M1.5 3 L7 7.5 L12.5 3"/></svg>
      </li>
    </ul>
  </section>

</main>
</body>
</html>
```